Harborview Estates Business Card for Apartment Buildings

Create business cards for resident managers who run apartment buildings. The audience is the public who are searching for apartment rentals, and current residents who live at the apartment building. Key design element will be incorporating the company logo, however, the logo cannot dominate. The building name and manager name are more important than the logo. Current business card design leaves little room for copy, so we may need to reduce the size on the current card to allow for more space for copy.

Target Market(s)

Adults 18-65 years of age, who are looking for an apartment rental, plus current residents who live at our apartment buildings.

Industry/Entity Type

Property Management

Contact Information for Business Card

A major design element will be use of the company logo. Important property and manager contact information must be part of the design. The size of the logo will need to be reduced to make room for building and manager contact copy.

Font styles to use
Sans Serif

Colors
3176b5
000000
959595
ffffff

Requirements
Must have
• 1) Incorporate the company logo.
• 2) Use the company colors (dark blue, black/grey, over white).
• 3) FEATURE THE BUILDING NAME
• 4) FEATURE THE MANAGER NAME
• 5) The company name is less important than BUILDING and MANAGER
• 6) Manager contact information
• **SEE ATTACHED CREATIVE BRIEF**
Nice to have
• 1) Back of card logo watermark
• 2) Ability to write notes on back of carfd
Should not have
• Avoid letting the company logo dominate the card, the building name and manager are more important than the company logo.

```html
<!DOCTYPE html>
<html lang="en">
<head>
<meta charset="utf-8">
<title>Harborview Estates Business Card</title>
<link rel="stylesheet" href="https://fonts.googleapis.com/css2?family=Roboto:wght@400;500;700;900&display=swap">
<style>
  :root {
    --blue: #0d5c9e;
    --black: #1d1d1f;
    --grey: #959595;
    --faint: #ececec;
    --white: #ffffff;
    --backdrop: #2b2b2d;
  }
  * { margin: 0; padding: 0; box-sizing: border-box; }
  html, body { width: 1200px; height: 880px; overflow: hidden; }
  body {
    background: var(--backdrop);
    font-family: "Roboto", Arial, sans-serif;
    position: relative;
  }
  .card {
    position: absolute;
    width: 700px;
    height: 400px;
    left: 250px;
    background: var(--white);
    border-radius: 22px;
    overflow: hidden;
    box-shadow: 0 10px 30px rgba(0,0,0,.45);
  }
  .card-back { top: 30px; }
  .card-front { top: 450px; }

  /* back */
  .back-band {
    position: absolute; left: 0; top: 0; width: 150px; height: 100%;
    background: var(--blue);
  }
  .back-brand {
    position: absolute; left: 75px; top: 200px;
    transform: translate(-50%, -50%) rotate(-90deg);
    display: flex; align-items: center; gap: 14px;
    white-space: nowrap;
  }
  .back-brand .mark {
    width: 34px; height: 34px; border-radius: 50%; background: var(--white);
  }
  .back-brand .name {
    color: var(--white); font-weight: 900; font-size: 30px; letter-spacing: 1px;
  }
  .watermark {
    position: absolute; left: 300px; top: 40px;
    width: 330px; height: 330px; border-radius: 50%;
    border: 14px solid var(--faint);
  }

  /* front */
  .front-shapes { position: absolute; inset: 0; }
  .front-watermark {
    position: absolute; left: 470px; top: 10px;
    width: 260px; height: 260px; border-radius: 50%;
    border: 12px solid var(--faint);
  }
  .brand {
    position: absolute; left: 60px; top: 78px;
    display: flex; align-items: center; gap: 16px;
  }
  .brand .mark {
    width: 58px; height: 58px; border-radius: 50%; background: var(--blue);
  }
  .brand .name {
    color: var(--blue); font-weight: 900; font-size: 38px; letter-spacing: .5px;
    white-space: nowrap;
  }
  .manager {
    position: absolute; left: 40px; top: 258px; color: var(--white);
  }
  .manager-name { font-weight: 700; font-size: 22px; letter-spacing: .5px; }
  .manager-title { font-weight: 400; font-size: 17px; }
  .contacts {
    position: absolute; left: 40px; top: 318px; list-style: none;
    color: var(--white); font-size: 15px; line-height: 22px;
  }
  .contacts li { display: flex; align-items: center; gap: 10px; }
  .contacts svg { width: 14px; height: 14px; fill: var(--white); }
  .address {
    position: absolute; right: 40px; top: 200px; text-align: right;
    color: var(--white); font-size: 15px; line-height: 21px;
  }
</style>
</head>
<body>

<section class="card card-back" aria-label="Card back">
  <div class="watermark" aria-hidden="true"></div>
  <div class="back-band">
    <div class="back-brand">
      <span class="mark" aria-hidden="true"></span>
      <span class="name">HARBORVIEW ESTATES</span>
    </div>
  </div>
</section>

<section class="card card-front" aria-label="Card front">
  <div class="front-watermark" aria-hidden="true"></div>
  <svg class="front-shapes" viewBox="0 0 700 400" aria-hidden="true">
    <path d="M0,248 L300,248 Q322,248 326,228 L332,198 Q337,172 362,172 L700,172 L700,400 L0,400 Z" fill="var(--black)"/>
    <path d="M0,306 L316,306 Q336,306 340,286 L346,206 Q350,184 374,184 L700,184 L700,400 L0,400 Z" fill="var(--blue)"/>
  </svg>

  <div class="brand">
    <span class="mark" aria-hidden="true"></span>
    <span class="name">HARBORVIEW ESTATES</span>
  </div>

  <div class="manager">
    <p class="manager-name">DANIEL BROOKS</p>
    <p class="manager-title">Property Manager</p>
  </div>

  <ul class="contacts">
    <li><svg viewBox="0 0 16 16"><path d="M3 1h3l1.5 4-2 1.3a9 9 0 0 0 4.2 4.2L11 8.5l4 1.5v3a2 2 0 0 1-2 2A13 13 0 0 1 1 3a2 2 0 0 1 2-2z"/></svg>555-214-7730</li>
    <li><svg viewBox="0 0 16 16"><path d="M4 1h8v4H4zM1 6h14v7h-3v2H4v-2H1zM5 10v4h6v-4z"/></svg>555-214-7731</li>
    <li><svg viewBox="0 0 16 16"><path d="M1 3h14v10H1zM2 4l6 5 6-5z" fill-rule="evenodd"/></svg>daniel@harborviewestates.com</li>
  </ul>

  <address class="address" style="font-style:normal">
    1280 Crescent Bay Road #B210<br>
    Bayside, CA 90417<br>
    www.harborviewestates.com
  </address>
</section>

</body>
</html>
```